Condo Debts Collection Business needs a Web Design (Contest)

I need a site for a client, who works with condo debts collection, and ensure all revenues provided by condo fees will be always available to the building manager of condo on a specific date, regardless of defaults.I have the logo of the companies, and some requirements on layout (kind of slider, menu options, phone number on a noble position, etc).
Updates

Designs look the same

Target Market(s)

I have two targets for this design: - Condominium's building manager. This target is looking for a solution to overdue debts on it's condo. - Residents on condominiums. This target wants to live in a better place, where their neighbors pay their condominium fees on time.

Number of Pages Required

1 page

Requirements
Must have
• - Slider with title, some short text related, a nice image (I prefer happy and/or peaceful family, people doing business, happy friends, and so on).
• - I have a special attention to menu. I'm looking for one I can have a nice effect, more elegant, charming, kind of innovative.
• - Phone number on the top (or clearly visible).
• - Member log in area or icon on the top (or clearly visible).
• - News/articles area.
• - Modern fonts, with good quality, sans-serif on areas where reading is more intensive (prefer Google web-fonts).
• - Colors specified on attached files.
• - Header similar or inspired by the "FILE 3"
Nice to have
• - Clear background color, cause it's better to read larger texts (like articles). Dark backgrounds makes reading difficult.
• - A site with effects (like shadows, lines, gradients, lights) is usually pretty.
• - I pay attention on beautiful footers.
Should not have
• - Images with a lot of money (I don't sell richness, I sell tranquility, peace, harmony, safety).
• - Poor menu.
• - Lots of curves. My customer asked for straight lines.

```html
<!DOCTYPE html>
<html lang="en">
<head>
<meta charset="utf-8">
<title>Pazendra – Condo Fee Assurance</title>
<link href="https://fonts.googleapis.com/css2?family=Lato:wght@400;700;900&display=swap" rel="stylesheet">
<style>
:root{
  --navy:#142f66;
  --navy-dark:#0f2552;
  --orange:#e8690f;
  --orange-light:#f08a2a;
  --text:#555;
  --muted:#8a8a8a;
  --grey-bg:#f1f1f1;
  --ghost:#f3f3f3;
  --white:#fff;
}
*{box-sizing:border-box;margin:0;padding:0}
html,body{width:1200px;height:3536px;overflow:hidden}
body{font-family:'Lato',sans-serif;color:var(--text);background:var(--white);position:relative}
.abs{position:absolute}

/* header */
.brand{left:113px;top:38px;display:flex;align-items:center;gap:12px}
.brand-mark{width:34px;height:34px;background:var(--navy)}
.brand-name{font-weight:900;font-size:30px;color:var(--navy);letter-spacing:.5px}
.call{left:588px;top:34px;display:flex;align-items:center;gap:14px}
.call-icon{width:64px;height:64px;border:3px solid var(--orange);border-radius:50%;display:flex;align-items:center;justify-content:center}
.call-label{font-size:17px;font-weight:700;color:#222}
.call-number{font-size:28px;font-weight:700;color:#111}
.login{left:872px;top:38px;width:214px;height:54px;border-radius:27px;background:var(--navy);color:var(--white);font-weight:700;font-size:18px;display:flex;align-items:center;justify-content:center}

.nav{left:0;top:141px;width:1200px;height:48px;background:linear-gradient(#f08a2a,#d85d08);display:flex;padding-left:276px}
.nav a{color:var(--white);text-decoration:none;font-size:16px;font-weight:700;height:48px;display:flex;align-items:center;padding:0 20px}
.nav a.active{background:var(--navy);text-decoration:underline;text-decoration-color:var(--orange);text-underline-offset:6px}

/* hero */
.hero{left:0;top:189px;width:1200px;height:629px;background:linear-gradient(180deg,#c7ccd2 0%,#e4d6bd 45%,#b9803a 75%,#7a4b1c 100%)}
.hero-panel{left:585px;top:330px;width:615px;height:300px;background:rgba(20,47,102,.82);text-align:center;color:var(--white)}
.hero-title{font-size:64px;font-weight:700;margin-top:38px;letter-spacing:1px}
.hero-sub{font-size:20px;margin-top:18px}
.hero-btn{display:inline-block;margin-top:28px;width:165px;height:50px;line-height:50px;border-radius:25px;background:linear-gradient(var(--orange-light),var(--orange));font-size:14px;font-weight:700}
.dots{left:535px;top:760px;display:flex;gap:8px;align-items:center}
.dots span{width:8px;height:8px;border-radius:50%;background:var(--white)}
.dots .arrow{width:22px;height:22px;display:flex;align-items:center;justify-content:center;color:#333;font-size:12px;font-weight:900;background:var(--white)}

/* headings */
.ghost{font-weight:900;color:var(--ghost);font-size:96px;white-space:nowrap;line-height:1}
.section-title{font-size:48px;font-weight:900;color:var(--navy);line-height:1.2}
.rule{width:66px;height:3px;background:var(--orange)}

/* about */
.about-text{left:113px;top:1008px;width:420px;font-size:15px;line-height:29px;color:var(--muted)}
.about-text p+p{margin-top:14px}
.btn{background:linear-gradient(var(--orange-light),var(--orange));color:var(--white);font-weight:700;font-size:15px;display:flex;align-items:center;justify-content:center;gap:8px;border-radius:28px}
.about-frame{left:646px;top:934px;width:482px;height:376px;border:4px solid var(--orange)}
.about-photo{left:604px;top:964px;width:483px;height:381px;background:linear-gradient(135deg,#e9e4da,#c9bca6 60%,#a59478)}

/* services */
.services{left:0;top:1462px;width:1200px;height:760px;background:var(--grey-bg)}
.ring{left:460px;top:1781px;width:282px;height:282px;border:8px solid var(--orange);border-radius:50%}
.node{width:26px;height:26px;border:5px solid var(--navy);background:var(--white);border-radius:50%}
.hub{left:531px;top:1908px;width:140px;text-align:center;font-size:18px;font-weight:900;color:var(--navy)}
.svc-icon{width:86px;height:86px;border-radius:50%;display:flex;align-items:center;justify-content:center}
.svc-icon.navy{background:var(--navy)}
.svc-icon.orange{background:linear-gradient(var(--orange-light),var(--orange))}
.svc{width:240px}
.svc h3{font-size:23px;font-weight:700;color:#222;margin-bottom:10px}
.svc p{font-size:13px;line-height:26px;color:var(--muted)}
.svc.right-align{text-align:right}

/* news */
.card{background:var(--white);border:1px solid #ececec}
.card.featured{box-shadow:0 0 12px rgba(0,0,0,.18)}
.news-photo{background:linear-gradient(135deg,#d9d1c4,#b59d7f)}
.news-head{display:flex;gap:10px;align-items:flex-start}
.news-mark{width:24px;height:24px;background:var(--navy);flex:none;margin-top:6px}
.news-head h4{font-size:20px;font-weight:700;color:#222;line-height:24px;width:230px}
.news-body{font-size:13px;line-height:24px;color:var(--muted);margin-top:10px}
.meta{font-size:13px;color:#444;margin-top:10px;display:flex;gap:6px;align-items:center}
.meta i{width:9px;height:9px;border-radius:50%;background:var(--orange);display:inline-block}
.outline-btn{width:132px;height:42px;border:2px solid var(--orange);border-radius:21px;display:flex;align-items:center;justify-content:center;font-weight:700;font-size:14px;color:#222;margin-top:24px}

/* footer */
.footer{left:0;top:3131px;width:1200px;height:363px;background:var(--navy);border-top:5px solid var(--orange)}
.contact{width:280px;text-align:center;color:var(--white)}
.contact-icon{width:80px;height:80px;margin:0 auto;border:3px solid var(--white);border-radius:50%;display:flex;align-items:center;justify-content:center}
.contact-icon.filled{background:var(--orange);border-color:var(--orange)}
.contact h5{font-size:18px;font-weight:700;margin-top:14px}
.contact p{font-size:13px;line-height:24px;margin-top:4px}
.foot-rule{left:113px;top:3396px;width:975px;height:1px;background:rgba(255,255,255,.2)}
.foot-links{left:113px;top:3432px;display:flex;gap:22px;color:var(--white);font-size:14px;font-weight:700}
.social{left:888px;top:3422px;display:flex;gap:10px}
.social span{width:42px;height:42px;border:2px solid var(--white);border-radius:50%}
.copy-bar{left:0;top:3494px;width:1200px;height:42px;background:var(--navy-dark)}
.copy{left:0;top:3494px;width:700px;height:42px;background:var(--orange);color:var(--white);font-size:13px;display:flex;align-items:center;padding-left:93px}
</style>
</head>
<body>

<!-- header -->
<div class="abs brand"><span class="brand-mark"></span><span class="brand-name">PAZENDRA</span></div>
<div class="abs call">
  <div class="call-icon"><svg width="28" height="28" viewBox="0 0 24 24"><path fill="#142f66" d="M6.6 10.8a15.1 15.1 0 0 0 6.6 6.6l2.2-2.2c.3-.3.7-.4 1-.2 1.1.4 2.3.6 3.6.6.6 0 1 .4 1 1V20c0 .6-.4 1-1 1C10.6 21 3 13.4 3 4c0-.6.4-1 1-1h3.5c.6 0 1 .4 1 1 0 1.3.2 2.5.6 3.6.1.3 0 .7-.2 1z"/></svg></div>
  <div><div class="call-label">CALL US TODAY</div><div class="call-number">1 800 555 0142</div></div>
</div>
<div class="abs login">MEMBER LOGIN</div>

<nav class="abs nav">
  <a class="active">HOME</a><a>ABOUT US</a><a>SERVICES</a><a>REVIEWS</a><a>BLOG</a><a>CONTACT US</a>
</nav>

<!-- hero -->
<div class="abs hero" role="img" aria-label="Photo of a happy family walking hand in hand through a sunny field"></div>
<div class="abs hero-panel">
  <div class="hero-title">PAZENDRA</div>
  <div class="hero-sub">Sed ut perspiciatis unde omnis isteatem accusantium doloremque</div>
  <div class="hero-btn">GET STARTED</div>
</div>
<div class="abs dots"><span class="arrow">‹</span><span></span><span></span><span></span><span></span><span></span><span class="arrow">›</span></div>

<!-- about -->
<div class="abs ghost" style="left:0;top:897px">ABOUT US</div>
<h2 class="abs section-title" style="left:113px;top:903px">ABOUT US</h2>
<div class="abs rule" style="left:113px;top:966px"></div>
<div class="abs about-text">
  <p>Sed ut perspiciatis unde omnis iste natus error sit voluptatem accusantium doloremque laudantium, totore veritatis et quasi architecto beatae vitae dicta sunt explicabo. ipsam voluptatem quia voluptas sit aspernatur aut odit aut fugit</p>
  <p>Ut enim ad minima veniam, quis nostrum exercitationem ullam corporis suscipit laboriosam, nisi ut aliquid ex ea commodi consequatur</p>
</div>
<div class="abs btn" style="left:113px;top:1273px;width:173px;height:55px">READ MORE <span>›</span></div>
<div class="abs about-frame"></div>
<div class="abs about-photo" role="img" aria-label="Photo of an older couple reviewing documents with an advisor"></div>
<svg class="abs" style="left:792px;top:1102px" width="106" height="106" viewBox="0 0 106 106"><circle cx="53" cy="53" r="48" fill="rgba(255,255,255,.2)" stroke="#fff" stroke-width="6"/><path d="M42 33 L74 53 L42 73Z" fill="#fff"/></svg>

<!-- services -->
<div class="abs services"></div>
<div class="abs ghost" style="left:690px;top:1566px;color:#e8e8e8">WHAT WE DO</div>
<h2 class="abs section-title" style="left:0;width:1200px;text-align:center;top:1573px">OUR SERVICES</h2>
<div class="abs rule" style="left:567px;top:1636px"></div>

<div class="abs ring"></div>
<div class="abs node" style="left:474px;top:1830px"></div>
<div class="abs node" style="left:701px;top:1830px"></div>
<div class="abs node" style="left:474px;top:1984px"></div>
<div class="abs node" style="left:701px;top:1984px"></div>
<div class="abs hub">PAZENDRA</div>

<div class="abs svc-icon navy" style="left:384px;top:1740px"><svg width="40" height="40" viewBox="0 0 24 24" fill="none" stroke="#fff" stroke-width="2"><rect x="3" y="5" width="14" height="15" rx="1"/><path d="M10 14 L19 5 L21 7 L12 16 L9 17Z"/></svg></div>
<div class="abs svc-icon orange" style="left:730px;top:1740px"><svg width="40" height="40" viewBox="0 0 24 24" fill="none" stroke="#fff" stroke-width="2"><path d="M3 20h18M4 16l5-5 4 3 7-7M16 7h4v4"/></svg></div>
<div class="abs svc-icon orange" style="left:358px;top:1987px"><span style="color:#fff;font-size:40px;font-weight:900">$</span></div>
<div class="abs svc-icon navy" style="left:756px;top:1987px"><svg width="44" height="36" viewBox="0 0 30 24" fill="#fff"><circle cx="15" cy="7" r="4"/><circle cx="6" cy="9" r="3"/><circle cx="24" cy="9" r="3"/><path d="M8 22c0-5 3-8 7-8s7 3 7 8z"/><path d="M0 21c0-4 2-7 6-7 1 0 2 .3 3 1-2 1.5-3 4-3 6z"/><path d="M30 21c0-4-2-7-6-7-1 0-2 .3-3 1 2 1.5 3 4 3 6z"/></svg></div>

<div class="abs svc right-align" style="left:120px;top:1730px"><h3>Sed uerspiciatis</h3><p>But I must explain to you how all this mistaken idea of denouncing pleasuri give youlete account</p></div>
<div class="abs svc" style="left:842px;top:1730px"><h3>Sed uerspiciatis</h3><p>But I must explain to you how all this mistaken idea of denouncing pleasuri give youlete account</p></div>
<div class="abs svc right-align" style="left:94px;top:1978px"><h3>Sed uerspiciatis</h3><p>But I must explain to you how all this mistaken idea of denouncing pleasuri give youlete account</p></div>
<div class="abs svc" style="left:868px;top:1978px"><h3>Sed uerspiciatis</h3><p>But I must explain to you how all this mistaken idea of denouncing pleasuri give youlete account</p></div>

<!-- news -->
<div class="abs ghost" style="left:-210px;top:2326px">LATEST NEWS</div>
<h2 class="abs section-title" style="left:0;width:1200px;text-align:center;top:2333px">LATEST NEWS</h2>
<div class="abs rule" style="left:567px;top:2396px"></div>

<div class="abs card featured" style="left:113px;top:2481px;width:344px;height:514px">
  <div class="news-photo" style="margin:11px;height:215px" role="img" aria-label="Photo of a young man and an older woman reviewing papers"></div>
  <div style="padding:12px 20px">
    <div class="news-head"><span class="news-mark"></span><h4>At vero eos ccusamiusto odio dignissimos</h4></div>
    <p class="news-body">Ut enim ad minima veniam, quis nostreirci isi orioodi eprehenderitq utate velit .</p>
    <div class="meta"><i></i>Admin &nbsp;|&nbsp; <i></i>4 comments</div>
    <div class="outline-btn">READ MORE</div>
  </div>
</div>

<div class="abs card" style="left:486px;top:2481px;width:600px;height:245px">
  <div class="abs news-photo" style="left:11px;top:11px;width:222px;height:222px" role="img" aria-label="Photo of a woman smiling while reading a document"></div>
  <div class="abs" style="left:268px;top:30px;width:300px">
    <div class="news-head"><span class="news-mark"></span><h4>At vero eos ccusamiusto odio dignissimos</h4></div>
    <p class="news-body">Ut enim ad minima veniam, quis nostreirci tationem ullam corporis suscipit laborisan isi orioodi eprehenderitq utate velit .</p>
    <div class="meta"><i></i>Admin &nbsp;|&nbsp; <i></i>4 comments</div>
  </div>
</div>

<div class="abs card" style="left:486px;top:2752px;width:600px;height:245px">
  <div class="abs news-photo" style="left:11px;top:11px;width:222px;height:222px" role="img" aria-label="Photo of a smiling couple embracing at home"></div>
  <div class="abs" style="left:268px;top:30px;width:300px">
    <div class="news-head"><span class="news-mark"></span><h4>At vero eos ccusamiusto odio dignissimos</h4></div>
    <p class="news-body">Ut enim ad minima veniam, quis nostreirci tationem ullam corporis suscipit laborisan isi orioodi eprehenderitq utate velit .</p>
    <div class="meta"><i></i>Admin &nbsp;|&nbsp; <i></i>4 comments</div>
  </div>
</div>

<!-- footer -->
<footer class="abs footer"></footer>
<div class="abs contact" style="left:51px;top:3183px">
  <div class="contact-icon"><svg width="34" height="34" viewBox="0 0 24 24"><path fill="#fff" d="M6.6 10.8a15.1 15.1 0 0 0 6.6 6.6l2.2-2.2c.3-.3.7-.4 1-.2 1.1.4 2.3.6 3.6.6.6 0 1 .4 1 1V20c0 .6-.4 1-1 1C10.6 21 3 13.4 3 4c0-.6.4-1 1-1h3.5c.6 0 1 .4 1 1 0 1.3.2 2.5.6 3.6.1.3 0 .7-.2 1z"/></svg></div>
  <h5>PHONE</h5><p>(+428) 555 014 2200</p>
</div>
<div class="abs contact" style="left:292px;top:3183px">
  <div class="contact-icon"><svg width="30" height="36" viewBox="0 0 24 30"><path fill="none" stroke="#fff" stroke-width="2.5" d="M12 28C5 19 3 15 3 11a9 9 0 0 1 18 0c0 4-2 8-9 17z"/><circle cx="12" cy="11" r="3.5" fill="#fff"/></svg></div>
  <h5>HEAD OFFICE</h5><p>47 Linden Harbor Avenue, Eastgate,<br>Norfield, USA, PO-5310</p>
</div>
<div class="abs contact" style="left:591px;top:3183px">
  <div class="contact-icon filled"><svg width="30" height="36" viewBox="0 0 24 30"><path fill="none" stroke="#fff" stroke-width="2.5" d="M12 28C5 19 3 15 3 11a9 9 0 0 1 18 0c0 4-2 8-9 17z"/><circle cx="12" cy="11" r="3.5" fill="#fff"/></svg></div>
  <h5>MAIN OFFICE</h5><p>47 Linden Harbor Avenue, Eastgate,<br>Norfield, USA, PO-5310</p>
</div>
<div class="abs contact" style="left:857px;top:3183px">
  <div class="contact-icon"><svg width="34" height="26" viewBox="0 0 24 18"><rect x="1" y="1" width="22" height="16" rx="2" fill="#fff"/><path d="M2 2l10 8 10-8" fill="none" stroke="#142f66" stroke-width="2"/></svg></div>
  <h5>EMAIL</h5><p>hello@pazendracondo.com</p>
</div>
<div class="abs foot-rule"></div>
<div class="abs foot-links"><span>HOME</span><span>|</span><span>ABOUT US</span><span>|</span><span>SERVICES</span><span>|</span><span>REVIEWS</span><span>|</span><span>BLOG</span><span>|</span><span>CONTACT US</span></div>
<div class="abs social"><span></span><span></span><span></span><span></span></div>
<div class="abs copy-bar"></div>
<div class="abs copy">Copyrights © 2019, Pazendra. All rights reserved &nbsp;|&nbsp; Privacy Policy &nbsp;|&nbsp; Terms of use</div>

</body>
</html>
```